Need a stunning home page for Car rental company

For a client, I need a slick and sumber home page design. It is a small, local car rental company, with a handful of cars available for rent.
Selling points: affordable lease, availability, always clean cars
The design should be:
- flat and modern
- no, or very few animations/sliders
- CTA: booking form for renting a car.
- 3 featured cars with images and facts (see website) with button to read more about the car.
- fullscreen background video can be an option
- main colour: #efba01
The site is under construction here:
http://solvikutleie.hammerlia.no/
Delivery requirements:
I need a layered & well organised PSD file delivered.

```html
<!DOCTYPE html>
<html lang="no">
<head>
<meta charset="utf-8">
<title>Solvik Utleie – Bilutleie</title>
<link rel="stylesheet" href="https://fonts.googleapis.com/css2?family=Open+Sans:wght@400;600;700&display=swap">
<style>
:root{
  --brand:#efba01;
  --ink:#111;
  --white:#fff;
  --muted:#9a9a9a;
  --card:#262626;
  --cell:#333;
  --line:#1f1f1f;
  --footer:#0b0b0b;
}
*{margin:0;padding:0;box-sizing:border-box}
html,body{width:780px;height:1200px;overflow:hidden;background:#000}
body{font-family:"Open Sans",Arial,sans-serif;color:var(--white);position:relative}
.abs{position:absolute}

/* hero */
.hero{position:absolute;left:0;top:0;width:780px;height:437px;overflow:hidden;
  background:linear-gradient(160deg,#2a2a28 0%,#5a5852 35%,#3b3a36 60%,#141413 100%)}
.hero-photo{position:absolute;left:130px;top:90px;width:530px;height:230px;border-radius:120px 160px 60px 60px;
  background:radial-gradient(ellipse at 50% 45%,#8a877f 0%,#5e5c56 45%,rgba(40,40,38,0) 75%)}
.nav{position:absolute;top:0;left:0;width:780px;height:52px}
.logo{position:absolute;left:24px;top:17px;font-weight:700;font-size:14px;letter-spacing:.5px;color:var(--white)}
.logo b{color:var(--brand);font-weight:700}
.nav-link{position:absolute;top:22px;font-size:7px;color:#ddd;letter-spacing:.2px}
.burger{position:absolute;left:693px;top:20px;width:16px}
.burger i{display:block;height:2px;background:#ddd;margin-bottom:3px}
.lang{position:absolute;left:719px;top:18px;width:47px;height:15px;border:1px solid #aaa;font-size:6px;line-height:13px;padding-left:7px;color:#ddd}
.lang:after{content:"";position:absolute;right:5px;top:5px;border:3px solid transparent;border-top-color:#ddd}
.play{position:absolute;left:368px;top:181px;width:43px;height:43px;border-radius:50%;border:2px solid rgba(255,255,255,.35)}
.play:after{content:"";position:absolute;left:17px;top:12px;border:8px solid transparent;border-left:11px solid rgba(255,255,255,.4)}
.play-label{position:absolute;left:340px;top:234px;width:100px;text-align:center;font-size:7px}
.dots{position:absolute;left:740px;top:180px}
.dots i{display:block;width:6px;height:6px;border:1px solid #777;margin-bottom:5px}
.dots i:first-child{background:#888}
.booking-kicker{position:absolute;left:35px;top:343px;font-size:10px;font-weight:600}
.booking-title{position:absolute;left:35px;top:353px;font-size:23px;font-weight:700;color:var(--brand)}
.btn-ghost{position:absolute;left:35px;top:386px;width:82px;height:20px;border:1px solid var(--white);font-size:7px;text-align:center;line-height:18px}
.scroll{position:absolute;left:320px;top:370px;width:140px;text-align:center;font-size:7px}
.scroll svg{display:block;margin:0 auto 8px}
.tagline-name{position:absolute;left:517px;top:352px;font-size:18px;color:var(--brand)}
.tagline{position:absolute;left:517px;top:385px;font-size:14px;font-weight:700}

/* welcome */
.welcome{position:absolute;left:0;top:437px;width:780px;height:190px;background:var(--white);text-align:center;color:var(--ink)}
.welcome h1{position:absolute;top:41px;width:100%;font-size:14px;font-weight:700}
.welcome-mark{position:absolute;top:71px;width:100%;font-size:16px;font-weight:700;color:#555}
.welcome-mark b{color:var(--brand)}
.lead{position:absolute;top:111px;left:130px;width:520px;font-size:6.6px;line-height:14px;color:var(--muted);text-transform:uppercase}

/* featured */
.featured{position:absolute;left:0;top:627px;width:780px;height:523px;background:linear-gradient(#000 0%,#0e0e0e 60%,#050505 100%)}
.featured-bg{position:absolute;left:20px;top:150px;width:740px;height:260px;border-radius:140px;
  background:radial-gradient(ellipse at 50% 50%,rgba(120,95,10,.55) 0%,rgba(60,48,8,.3) 50%,rgba(0,0,0,0) 75%)}
.featured h2{position:absolute;top:34px;width:100%;text-align:center;font-size:15px;font-weight:700;color:var(--brand)}
.featured .lead{top:66px;color:#888}
.card{position:absolute;top:121px;width:185px;height:355px;background:var(--card)}
.card-photo{height:117px}
.card h3{position:absolute;left:17px;top:130px;font-size:11px;font-weight:600}
.price{position:absolute;left:17px;top:149px;font-size:9px;font-weight:600}
.specs{position:absolute;left:16px;top:169px;width:154px;border-collapse:collapse;font-size:6.5px}
.specs td{height:19.5px;background:var(--cell);border-bottom:1px solid var(--card);padding-left:8px;color:#eee}
.specs td:first-child{width:76px;border-right:1px solid var(--card)}
.btn-card{position:absolute;left:16px;top:311px;width:154px;height:28px;border:1px solid #aaa;font-size:7px;font-weight:600;color:#aaa;text-align:center;line-height:26px}

/* footer */
.footer{position:absolute;left:0;top:1150px;width:780px;height:50px;background:var(--footer);font-size:6.5px;color:#ccc}
.footer .sep{position:absolute;top:15px;width:1px;height:22px;background:#333}
.footer-logo{position:absolute;left:16px;top:18px;font-size:10px;font-weight:700}
.footer-logo b{color:var(--brand)}
.social{position:absolute;top:21px;width:8px;height:8px;border-radius:50%;background:var(--brand)}
</style>
</head>
<body>

<header class="hero">
  <div class="hero-photo" role="img" aria-label="Silver sedan driving at speed, motion-blurred background video still"></div>
  <nav class="nav">
    <div class="logo">SOLVIK <b>UTLEIE</b></div>
    <span class="nav-link" style="left:237px">HJEM</span>
    <span class="nav-link" style="left:283px">BILPARKEN VÅR</span>
    <span class="nav-link" style="left:364px">TJENESTER</span>
    <span class="nav-link" style="left:428px">KONTAKT OSS</span>
    <span class="nav-link" style="left:505px">BLOG</span>
    <span class="nav-link" style="left:552px">PAGE TEMPLATES</span>
    <span class="nav-link" style="left:640px">ABOUT US</span>
    <div class="burger"><i></i><i></i><i></i></div>
    <div class="lang">ENGLISH</div>
  </nav>
  <div class="play"></div>
  <div class="play-label">PLAY VIDEO</div>
  <div class="dots"><i></i><i></i><i></i><i></i><i></i></div>

  <div class="booking-kicker">A BOOKING FORM TO</div>
  <div class="booking-title">RENT A CAR</div>
  <div class="btn-ghost">CLICK HERE</div>

  <div class="scroll">
    <svg width="12" height="12" viewBox="0 0 12 12"><path d="M2 1l4 4 4-4M2 6l4 4 4-4" fill="none" stroke="#aaa" stroke-width="1.5"/></svg>
    SCROLL DOWN FOR MORE
  </div>

  <div class="tagline-name">Solvik Utleie</div>
  <div class="tagline">WE ARE A CAR RENTAL COMPANY</div>
</header>

<section class="welcome">
  <h1>VELKOMMEN TIL SOLVIK UTLEIE – STRANDVIK</h1>
  <div class="welcome-mark">SOLVIK <b>UTLEIE</b></div>
  <p class="lead">Solvik Utleie er en bilpark på Strandvik, og leier ut varebiler og personbiler til deg som trenger en ekstrabil til flytting, ferie, bytur eller hva det måtte være. Vi er uslåelige på service, og mest sannsynlig også på pris. Og du kan stole på at bilen du får fra oss er både ren og pen!</p>
</section>

<section class="featured">
  <div class="featured-bg" role="img" aria-label="Blurred yellow sports car in dark background"></div>
  <h2>FEATURED CARS</h2>
  <p class="lead">Solvik Utleie er en bilpark på Strandvik, og leier ut varebiler og personbiler til deg som trenger en ekstrabil til flytting, ferie, bytur eller hva det måtte være. Vi er uslåelige på service</p>

  <article class="card" style="left:112px">
    <div class="card-photo" role="img" aria-label="Silver sedan in a curving tunnel" style="background:linear-gradient(135deg,#d8d8d8,#6e6e6e 60%,#3a3a3a)"></div>
    <h3>VAREBILEN</h3><div class="price">PRICE PER DAY : KR 600</div>
    <table class="specs">
      <tr><td>Biltype</td><td>Varebil</td></tr><tr><td>Maks. pers</td><td>2</td></tr><tr><td>Ant. dører</td><td>5</td></tr><tr><td>Min. sjåføralder</td><td>21</td></tr><tr><td>Girtype</td><td>Manuell</td></tr><tr><td>Klimaanlegg?</td><td>Ja</td></tr><tr><td>Ubegrenset km?</td><td>Nei</td></tr>
    </table>
    <div class="btn-card">READ MORE ABOUT THE CAR</div>
  </article>

  <article class="card" style="left:298px">
    <div class="card-photo" role="img" aria-label="Yellow hatchback in a dark garage" style="background:radial-gradient(ellipse at 55% 60%,#d8a800,#5a4a10 45%,#15151a 80%)"></div>
    <h3>VAREBILEN</h3><div class="price">PRICE PER DAY : KR 600</div>
    <table class="specs">
      <tr><td>Biltype</td><td>Varebil</td></tr><tr><td>Maks. pers</td><td>2</td></tr><tr><td>Ant. dører</td><td>5</td></tr><tr><td>Min. sjåføralder</td><td>21</td></tr><tr><td>Girtype</td><td>Manuell</td></tr><tr><td>Klimaanlegg?</td><td>Ja</td></tr><tr><td>Ubegrenset km?</td><td>Nei</td></tr>
    </table>
    <div class="btn-card">READ MORE ABOUT THE CAR</div>
  </article>

  <article class="card" style="left:484px">
    <div class="card-photo" role="img" aria-label="Red SUV parked on a mountain road at sunset" style="background:linear-gradient(160deg,#8a7e6e,#a05050 55%,#6e6a66)"></div>
    <h3>VAREBILEN</h3><div class="price">PRICE PER DAY : KR 600</div>
    <table class="specs">
      <tr><td>Biltype</td><td>Varebil</td></tr><tr><td>Maks. pers</td><td>2</td></tr><tr><td>Ant. dører</td><td>5</td></tr><tr><td>Min. sjåføralder</td><td>21</td></tr><tr><td>Girtype</td><td>Manuell</td></tr><tr><td>Klimaanlegg?</td><td>Ja</td></tr><tr><td>Ubegrenset km?</td><td>Nei</td></tr>
    </table>
    <div class="btn-card">READ MORE ABOUT THE CAR</div>
  </article>
</section>

<footer class="footer">
  <div class="footer-logo">SOLVIK <b>UTLEIE</b></div>
  <span class="sep" style="left:135px"></span>
  <span class="abs" style="left:152px;top:22px">© SOLVIK UTLEIE 2014. ALL RIGHTS RESERVED</span>
  <span class="sep" style="left:325px"></span>
  <svg class="abs" style="left:342px;top:18px" width="9" height="14" viewBox="0 0 9 14"><rect x="1" y="1" width="7" height="12" rx="1" fill="none" stroke="#ccc"/><rect x="3.5" y="10.5" width="2" height="1" fill="#ccc"/></svg>
  <span class="abs" style="left:357px;top:22px">QUESTION? CALL US : <span style="color:var(--brand)">91234567</span></span>
  <span class="sep" style="left:476px"></span>
  <span class="abs" style="left:493px;top:22px">CONNECT TO OUR SOCIAL NETWORK :</span>
  <span class="social" style="left:621px"></span>
  <span class="social" style="left:643px"></span>
  <span class="social" style="left:665px"></span>
  <span class="social" style="left:687px"></span>
  <span class="social" style="left:709px"></span>
</footer>

</body>
</html>
```